Residential real estate home builder in west texas

We need a website design for our home building business based in west Texas called Birch Hollow homes. We build new construction for potential homeowners in Amarillo. Currently we do not have any completed construction, but we have floor plans and architectural drawings of the front elevation. The website would need to be able to properly advertise a architectural drawing, floor plans, and descriptive content at the initial phase. The website will need to be simple but professional with generic picture content.
The website will need the ability to be updated in the future for the additions of home pictures, and video content and virtual tours of the homes.

Target Market(s)

Potential Home buyers

Industry/Entity Type

Real Estate

Number of Pages Required

5+ page

Font styles to use
Sans Serif

Colors
f37122
757575

Requirements
Must have
• Web design must be simple and easy to navigate. There is not much picture content, so it will need to be simple.
• 5 pages:
• Home, Available homes, Available floor plans, guide to ownership, Contact
• The website will need the ability to be updated in the future for the additions of pictures, and video content of the homes when they are built. ( A virtual tour).
Nice to have
• I would like to see a modern and cohesive design. Contact information at the bottom of each page.
Should not have
• A Black background

```html
<!DOCTYPE html>
<html lang="en">
<head>
<meta charset="utf-8">
<title>Birch Hollow Homes</title>
<link rel="stylesheet" href="https://fonts.googleapis.com/css2?family=Open+Sans:wght@300;400;600&family=Oswald:wght@400;500&display=swap">
<style>
:root{
  --orange:#f37122;
  --grey:#757575;
  --ink:#2b2b2b;
  --topbar:#6b6b6b;
  --soft:#f2f2f2;
  --white:#ffffff;
}
*{box-sizing:border-box;margin:0;padding:0}
html,body{width:1200px;height:2752px;overflow:hidden}
body{font-family:"Open Sans",Arial,sans-serif;color:var(--grey);background:var(--white);position:relative}
section,header,footer,div{position:relative}

/* top bar */
.topbar{height:37px;background:var(--topbar);color:var(--white);font-size:13px;display:flex;align-items:center;padding:0 92px;white-space:nowrap}
.topbar .contact-item{display:flex;align-items:center;gap:7px;margin-right:14px}
.topbar .divider{margin-right:14px}
.topbar .social{margin-left:auto;display:flex;gap:7px}
.topbar .social span{width:17px;height:17px;background:var(--white);border-radius:2px;opacity:.9}

/* header */
.site-header{height:104px;display:flex;align-items:center;padding:0 92px;box-shadow:0 2px 4px rgba(0,0,0,.08);z-index:2;background:var(--white)}
.brand{display:flex;align-items:center;gap:9px;color:var(--orange);font-weight:600;font-size:21px;letter-spacing:.5px;text-transform:uppercase;line-height:1;white-space:nowrap}
.brand .mark{width:14px;height:14px;background:var(--orange);flex:none}
.main-nav{margin-left:auto;display:flex;align-items:center;gap:34px;font-size:15px;color:var(--ink);text-transform:uppercase;white-space:nowrap}
.main-nav a{text-decoration:none;color:inherit}
.main-nav .active{color:var(--orange);border:1.5px solid var(--orange);border-radius:16px;padding:4px 15px}

/* hero */
.hero{height:485px;overflow:hidden}
.hero .backdrop{position:absolute;inset:0;background:linear-gradient(180deg,#2a64a3 0%,#5d8fbf 30%,#8c9aa6 55%,#6d7a6a 78%,#3e4a36 100%)}
.hero .play{position:absolute;left:569px;top:162px;width:62px;height:62px;border-radius:50%;background:rgba(40,40,40,.75)}
.hero .play svg{position:absolute;left:22px;top:17px}
.hero h1{position:absolute;top:244px;left:0;width:100%;text-align:center;font-family:"Oswald","Arial Narrow",sans-serif;font-weight:500;font-size:64px;color:var(--white);letter-spacing:1px;line-height:1}
.hero .tagline{position:absolute;top:324px;left:0;width:100%;text-align:center;font-size:25px;line-height:32px;color:var(--white);letter-spacing:1px}
.hero .arrows{position:absolute;left:1047px;top:420px;display:flex;gap:4px}
.hero .arrows span{width:24px;height:24px;border-radius:50%;background:rgba(60,60,60,.7);display:flex;align-items:center;justify-content:center}

.section-title{font-size:28px;font-weight:400;color:var(--ink);text-align:center;letter-spacing:.5px;text-transform:uppercase}

/* services */
.services{height:457px}
.services .section-title{position:absolute;top:84px;width:100%}
.service-card{position:absolute;top:159px;width:292px;height:217px;background:var(--white);box-shadow:0 1px 5px rgba(0,0,0,.2);text-align:center;padding-top:36px}
.service-card.featured{background:var(--orange);color:var(--white)}
.service-card h3{font-size:15px;font-weight:400;color:var(--ink);margin-top:12px;text-transform:uppercase}
.service-card.featured h3{color:var(--white)}
.service-card p{font-size:12px;line-height:19px;margin:4px auto 0;width:240px}
.service-card.featured p{color:var(--white)}
.btn-outline{display:inline-block;margin-top:10px;font-size:11px;color:var(--grey);border:1px solid #999;border-radius:12px;padding:3px 17px}
.featured .btn-outline{background:var(--white);color:var(--ink);border-color:var(--white)}

/* welcome */
.welcome{height:381px;background:var(--soft)}
.welcome h2{position:absolute;left:92px;top:86px;font-size:28px;font-weight:400;color:var(--ink);text-transform:uppercase;white-space:nowrap}
.welcome p{position:absolute;left:92px;top:134px;width:502px;font-size:12px;line-height:20.5px;text-align:justify}
.btn-solid{display:inline-block;background:var(--orange);color:var(--white);font-size:11px;border-radius:16px;padding:8px 19px}
.welcome .btn-solid{position:absolute;left:92px;top:274px;box-shadow:0 2px 3px rgba(0,0,0,.2)}
.welcome .video{position:absolute;left:637px;top:57px;width:473px;height:267px;border:5px solid var(--white);box-shadow:0 0 4px rgba(0,0,0,.25);background:linear-gradient(180deg,#26365c 0%,#55648a 40%,#c9a77a 70%,#3e6f8f 100%)}
.welcome .video .play{position:absolute;left:202px;top:101px;width:58px;height:58px;border-radius:50%;background:rgba(40,40,40,.7)}
.welcome .video .play svg{position:absolute;left:21px;top:16px}

/* projects */
.projects{height:573px}
.projects .section-title{position:absolute;top:83px;width:100%}
.project-card{position:absolute;top:154px;width:292px;height:309px;background:var(--white);box-shadow:0 1px 5px rgba(0,0,0,.2);text-align:center}
.project-card .photo{height:171px}
.project-card h3{font-size:15px;font-weight:400;color:var(--ink);margin-top:22px;text-transform:uppercase}
.project-card p{font-size:12px;line-height:19px;width:240px;margin:3px auto 0}
.project-card .btn-solid{margin-top:8px;padding:5px 19px}
.projects .nav-arrow{position:absolute;top:311px}

/* blog */
.blog{height:411px;background:var(--soft)}
.blog .section-title{position:absolute;top:55px;width:100%}
.post{position:absolute;top:134px;width:497px;height:189px;background:var(--white);box-shadow:0 1px 4px rgba(0,0,0,.15);display:flex}
.post .thumb{width:162px;height:189px;flex:none}
.post .body{padding:28px 22px 0 25px}
.post h3{font-size:15px;font-weight:400;color:var(--ink)}
.post .date{font-size:12px;font-style:italic;margin-top:9px}
.post p{font-size:11.5px;line-height:19px;margin-top:9px;color:#555}
.post .more{font-size:12px;color:var(--orange);margin-top:9px}

/* footer */
.site-footer{height:231px}
.site-footer .brand{position:absolute;left:92px;top:133px;font-size:19px}
.footer-col{position:absolute;top:76px}
.footer-col h4{font-size:14px;font-weight:400;color:var(--ink);text-transform:uppercase;margin-bottom:17px;white-space:nowrap}
.footer-col .lines{font-size:11.5px;line-height:22px}
.newsletter{display:flex;margin-top:12px}
.newsletter span{width:147px;height:31px;border:1px solid #ccc;font-size:11.5px;padding:7px 10px;color:#666}
.newsletter b{width:57px;height:31px;background:var(--orange);color:var(--white);font-weight:400;font-size:12px;padding:7px 9px}
.follow{display:flex;gap:10px}
.follow span{width:25px;height:25px;background:var(--grey);border-radius:4px}
.copyright{height:73px;background:#ececec;text-align:center;font-size:13px;line-height:73px;color:#555}
</style>
</head>
<body>

<div class="topbar">
  <span class="contact-item">
    <svg width="12" height="12" viewBox="0 0 24 24"><path fill="#fff" d="M6.6 10.8a15 15 0 0 0 6.6 6.6l2.2-2.2c.3-.3.7-.4 1-.2 1.1.4 2.3.6 3.6.6.6 0 1 .4 1 1V20c0 .6-.4 1-1 1A17 17 0 0 1 3 4c0-.6.4-1 1-1h3.5c.6 0 1 .4 1 1 0 1.3.2 2.5.6 3.6.1.3 0 .7-.2 1z"/></svg>
    806-555-0142
  </span>
  <span class="divider">|</span>
  <span class="contact-item">
    <svg width="13" height="10" viewBox="0 0 26 20"><rect x="1" y="1" width="24" height="18" rx="2" fill="none" stroke="#fff" stroke-width="2"/><path d="M1 2l12 9 12-9" fill="none" stroke="#fff" stroke-width="2"/></svg>
    hello@birchhollowhomes.com
  </span>
  <div class="social"><span></span><span></span><span></span><span></span></div>
</div>

<header class="site-header">
  <div class="brand"><span class="mark"></span>Birch Hollow Homes</div>
  <nav class="main-nav">
    <a class="active">Home</a>
    <a>Available Homes</a>
    <a>Available Floor Plans</a>
    <a>Guide to Ownership</a>
    <a>Contact</a>
  </nav>
</header>

<section class="hero">
  <div class="backdrop" role="img" aria-label="Photo of a modern glass office building with landscaped grounds under a blue sky"></div>
  <div class="play"><svg width="22" height="28" viewBox="0 0 22 28"><path d="M0 0l22 14L0 28z" fill="#fff"/></svg></div>
  <h1>VIRTUAL TOURS</h1>
  <div class="tagline">NEQUE PORRO QUISQUAM QUI DOLOREM</div>
  <div class="arrows">
    <span><svg width="8" height="10" viewBox="0 0 8 10"><path d="M6 1L2 5l4 4" stroke="#fff" stroke-width="1.6" fill="none"/></svg></span>
    <span><svg width="8" height="10" viewBox="0 0 8 10"><path d="M2 1l4 4-4 4" stroke="#fff" stroke-width="1.6" fill="none"/></svg></span>
  </div>
</section>

<section class="services">
  <h2 class="section-title">Our Services</h2>
  <div class="service-card" style="left:125px">
    <svg width="36" height="36" viewBox="0 0 24 24"><path fill="#f37122" d="M3 17.2V21h3.8L18 9.8 14.2 6zM20.7 7.1a1 1 0 0 0 0-1.4l-2.4-2.4a1 1 0 0 0-1.4 0l-1.8 1.8 3.8 3.8z"/></svg>
    <h3>Architectural Drawing</h3>
    <p>It has survived not only five centuries, but also the leap into electronic</p>
    <span class="btn-outline">View More</span>
  </div>
  <div class="service-card featured" style="left:455px">
    <svg width="36" height="36" viewBox="0 0 24 24"><path fill="#fff" d="M12 3L1 12h3v9h6v-6h4v6h6v-9h3z"/></svg>
    <h3>Floor Plans</h3>
    <p>It has survived not only five centuries, but also the leap into electronic</p>
    <span class="btn-outline">View More</span>
  </div>
  <div class="service-card" style="left:784px">
    <svg width="36" height="36" viewBox="0 0 24 24"><path fill="#f37122" d="M22.7 19l-9.1-9.1c.9-2.3.4-5-1.5-6.9-2-2-5-2.4-7.4-1.3L9 6 6 9 1.6 4.7C.4 7.1.9 10.1 2.9 12.1c1.9 1.9 4.6 2.4 6.9 1.5l9.1 9.1c.4.4 1 .4 1.4 0l2.3-2.3c.5-.4.5-1.1.1-1.4z"/></svg>
    <h3>Descriptive Content</h3>
    <p>It has survived not only five centuries, but also the leap into electronic</p>
    <span class="btn-outline">View More</span>
  </div>
</section>

<section class="welcome">
  <h2>Welcome to Birch Hollow Homes</h2>
  <p>It has survived not only five centuries, but also the leap into electronic typesetting, remaining essentially unchanged. It was popularised in the 1960s with the release of Lettermark sheets containing Lorem Ipsum passages, and more recently with desktop publishing software like PageForge including versions of Lorem Ipsum Ipsum as their default model text, and a search for 'lorem ipsum' will uncover many web sites still in their infancy.</p>
  <span class="btn-solid">Read More &raquo;</span>
  <div class="video" role="img" aria-label="Video still of a luxury home at dusk with palm trees and a lit swimming pool">
    <div class="play"><svg width="20" height="26" viewBox="0 0 22 28"><path d="M0 0l22 14L0 28z" fill="#fff"/></svg></div>
  </div>
</section>

<section class="projects">
  <h2 class="section-title">Our Projects</h2>
  <svg class="nav-arrow" style="left:68px" width="20" height="38" viewBox="0 0 20 38"><path d="M18 1L2 19l16 18" stroke="#aaa" stroke-width="1.5" fill="none"/></svg>
  <div class="project-card" style="left:134px">
    <div class="photo" role="img" aria-label="Photo of a two-storey suburban family house with garage at twilight" style="background:linear-gradient(180deg,#8fb3d6 0%,#c7d3de 45%,#6e6a66 75%,#4f6a3c 100%)"></div>
    <h3>Porro Quisquam</h3>
    <p>It has survived not only five centuries, but also the leap into electronic</p>
    <span class="btn-solid">View More</span>
  </div>
  <div class="project-card" style="left:455px">
    <div class="photo" role="img" aria-label="Photo of a modern flat-roofed home with glowing interior at night" style="background:linear-gradient(180deg,#1f2a3c 0%,#3c4454 45%,#b89a6a 75%,#3a3a36 100%)"></div>
    <h3>Dolorem Ipsum</h3>
    <p>It has survived not only five centuries, but also the leap into electronic</p>
    <span class="btn-solid">View More</span>
  </div>
  <div class="project-card" style="left:774px">
    <div class="photo" role="img" aria-label="Photo of a Mediterranean villa with terraces beside a pool" style="background:linear-gradient(180deg,#9ec3e0 0%,#d9c9b0 45%,#a86e4c 65%,#3f86b0 100%)"></div>
    <h3>Ipsum Quia Dolor</h3>
    <p>It has survived not only five centuries, but also the leap into electronic</p>
    <span class="btn-solid">View More</span>
  </div>
  <svg class="nav-arrow" style="left:1111px" width="20" height="38" viewBox="0 0 20 38"><path d="M2 1l16 18L2 37" stroke="#aaa" stroke-width="1.5" fill="none"/></svg>
</section>

<section class="blog">
  <h2 class="section-title">Latest Blog</h2>
  <article class="post" style="left:90px">
    <div class="thumb" role="img" aria-label="Photo of a yellow two-storey colonial house on a green lawn" style="background:linear-gradient(180deg,#7fb2e0 0%,#d8c98a 45%,#c9b56a 70%,#4f8a34 100%)"></div>
    <div class="body">
      <h3>Nemo Enim Ipsam Volup</h3>
      <div class="date">09-07-2017</div>
      <p>Lorem Ipsum has been the industry's standard dummy text ever since the 1500s, when an unknown printer took a galley of type and scrambled it to make</p>
      <div class="more">Read More &gt;&gt;</div>
    </div>
  </article>
  <article class="post" style="left:615px">
    <div class="thumb" role="img" aria-label="Photo of a large timber and stone craftsman home with front steps" style="background:linear-gradient(180deg,#9cc0de 0%,#8a6a4c 45%,#6c5844 70%,#7a8a5a 100%)"></div>
    <div class="body">
      <h3>Nemo Enim Ipsam Volup</h3>
      <div class="date">09-07-2017</div>
      <p>Lorem Ipsum has been the industry's standard dummy text ever since the 1500s, when an unknown printer took a galley of type and scrambled it to make</p>
      <div class="more">Read More &gt;&gt;</div>
    </div>
  </article>
</section>

<footer class="site-footer">
  <div class="brand"><span class="mark"></span>Birch Hollow Homes</div>
  <div class="footer-col" style="left:363px">
    <h4>Contact Us</h4>
    <div class="lines">Address : 412 Canyon Ridge Rd,<br>Amarillo, TX 79101<br>Phone : 806-555-0187<br>Email : hello@birchhollowhomes.com</div>
  </div>
  <div class="footer-col" style="left:640px">
    <h4>Sign Up for Newsletter</h4>
    <div class="lines" style="line-height:18px">Your about us information would fit<br>here nicely.</div>
    <div class="newsletter"><span>Email address</span><b>Submit</b></div>
  </div>
  <div class="footer-col" style="left:938px">
    <h4>Follow Us Out There</h4>
    <div class="follow"><span></span><span></span><span></span><span></span></div>
  </div>
</footer>

<div class="copyright">Copyright &copy; 2017. All Rights Reserved</div>

</body>
</html>
```